Modernize Website: marcusfellwright.net

I am a novelist with an older-generation website at: marcusfellwright.net.

I am hoping to refresh this outdated website with a new, responsive redesign. I would prefer to host the code myself, and edit using Adobe Dreamweaver. So I’m not looking to use a hosted site builder like Plexo. Nor am I looking to use a CMS like Pagecraft.

In order to simplify the old site, there are a number of sections I’ll be looking to remove during this redesign. These are shown in the "MF Site Redesign" attachment. I can also provide imagery for new content (another book series in addition to the existing one), as well as higher-resolution imagery (if needed) of the old content.

Happy to answer any further questions.
Updates

I've uploaded a ZIP file containing high-res artwork associated with the new trilogy of books.

Target Market(s)

Readers of epic fantasy novels such as H.W.B. Castellane's THE WARDEN OF THE VALES, Harold P.Q. Ventris's A CROWN OF ASH AND RAIN, Victor Halloway's THE GATE OF STARS, or Dennis Vale's BLADE OF MERIVANE.

Industry/Entity Type

Entertainment

Coding

Coded - Design and coding required

Number of Pages Required

5+ page

Font styles to use
Serif
Decorative

Colors

Designer to choose colors to be used in the design.

Requirements
Must have
• I'm looking for a responsive design that displays nicely on both mobile and desktop devices. Existing site contains multiple pages, but these can obviously be combined into fewer pages (or even one) by divisions such as tabs, sections, and/or modal windows. See marcusfellwright.net for current content and "MF Site Redesign" attachment for content to be removed at this time.
Nice to have
• The ability to fulfill orders of autographed books directly from the website. I currently use Coinlo to do this, but it would be nice to incorporate a more comprehensive merchant service at a reasonable rate.
Should not have
• I'd like to host and control the site code myself. So please don't use a hosted web builder like Plexo, or a cloud-based CMS like Pagecraft.

```html
<!DOCTYPE html>
<html lang="en">
<head>
<meta charset="utf-8">
<title>Marcus Fellwright — The Legend of Oraveth</title>
<link href="https://fonts.googleapis.com/css2?family=Abril+Fatface&family=Montserrat:wght@400;600;700&family=Playfair+Display:wght@400;700&family=Work+Sans:wght@400;600&display=swap" rel="stylesheet">
<style>
:root{
  --black:#000;
  --white:#fff;
  --red:#f5333f;
  --red-deep:#a5101a;
  --grey-text:#6f6f6f;
  --grey-shadow:#6b6b6b;
  --frame:#8a8a8a;
  --social-blue:#3b5a9a;
  --social-sky:#2f9ad8;
  --social-navy:#223a78;
}
*{margin:0;padding:0;box-sizing:border-box}
html,body{width:1200px;height:3509px;overflow:hidden;background:var(--white)}
body{position:relative;font-family:"Work Sans",Arial,sans-serif}
section,header,footer{position:absolute;left:0;width:1200px}
.abs{position:absolute}
.center{left:0;width:1200px;text-align:center}
.serif{font-family:"Playfair Display",Georgia,serif}

/* header */
.site-header{top:0;height:164px;background:var(--black)}
.brand{left:84px;top:46px;font-family:"Playfair Display",Georgia,serif;font-size:30px;line-height:34px;color:var(--white);display:flex;align-items:center;gap:14px}
.brand-mark{width:16px;height:16px;background:var(--red)}
.main-nav a{position:absolute;top:72px;font-family:"Playfair Display",Georgia,serif;font-size:17px;color:var(--white);text-decoration:none}
.main-nav a.active{color:var(--red)}
.nav-blade{left:713px;top:98px;width:100px;height:10px}

/* hero */
.hero{top:164px;height:470px;background:radial-gradient(ellipse at 75% 70%,#8a2c10 0%,#3b1a10 30%,#1c1c1e 60%),linear-gradient(#2a2a2c,#141414)}
.hero-art{inset:0;background:linear-gradient(180deg,rgba(60,62,66,.9) 0%,rgba(30,28,28,.6) 55%,rgba(120,40,10,.55) 100%)}
.hero-title{top:128px;font-family:"Abril Fatface",Georgia,serif;font-size:82px;line-height:96px;color:#fbe9ea;text-shadow:0 0 2px var(--red),2px 2px 0 var(--red-deep)}
.hero-sub{top:232px;font-family:"Montserrat",Arial,sans-serif;font-size:24px;line-height:33px;color:var(--white);font-weight:600}
.btn{display:block;background:var(--red);color:var(--white);font-family:"Montserrat",Arial,sans-serif;font-weight:600;font-size:14px;text-align:center}
.hero .btn{left:512px;top:311px;width:178px;height:37px;line-height:37px}

/* shared section headings */
.section-title{font-family:"Playfair Display",Georgia,serif;font-size:54px;line-height:64px}
.blade{height:22px;width:273px;left:487px;background:linear-gradient(90deg,#3a0004 0%,var(--red-deep) 25%,var(--red) 70%,#d8d8d8 82%,#9a9a9a 100%);border-radius:0 11px 11px 0}
.tabs a{position:absolute;font-family:"Playfair Display",Georgia,serif;font-size:22px;line-height:42px;text-decoration:none;white-space:nowrap}
.tabs a.active{background:var(--red);color:var(--white);text-align:center}
.sub-title{font-family:"Playfair Display",Georgia,serif;font-size:42px;line-height:52px;color:var(--red)}

/* novels */
.novels{top:634px;height:833px;background:var(--white)}
.novels .section-title{top:111px;color:#222}
.novels .blade{top:170px}
.novels .tabs a{top:236px;color:#222}
.novels .sub-title{top:306px}
.novels .lead{top:371px;font-size:16px;color:var(--grey-text)}
.book-card{top:421px;width:210px;height:288px;background:var(--black);color:var(--white);text-align:center;font-family:"Playfair Display",Georgia,serif;font-size:16px}
.book-card.featured{background:var(--red);color:#111}
.book-card .book-no{position:absolute;top:30px;left:0;width:100%}
.book-card .cover{position:absolute;top:70px;left:60px;width:90px;height:134px;border:2px solid #ddd}
.book-card .book-name{position:absolute;top:222px;left:0;width:100%}

/* world */
.world{top:1467px;height:818px;background:var(--black)}
.world .section-title{top:89px;color:var(--red)}
.world .blade{top:150px}
.world .tabs a{top:210px;color:var(--white)}
.world .sub-title{top:282px}
.world .lead{top:346px;left:240px;width:720px;text-align:center;font-size:16px;line-height:28px;color:var(--white)}
.gallery-item{top:467px;width:326px;height:254px;border:2px solid var(--frame)}

/* author */
.author{top:2285px;height:845px;background:var(--white)}
.author .section-title{top:85px;color:#222}
.author .blade{top:148px}
.author .tabs a{top:213px;color:#222}
.bio-title{left:126px;top:297px}
.bio-text{left:131px;top:368px;width:615px;font-size:15px;line-height:26.4px;color:var(--grey-text)}
.bio-text p+p{margin-top:26px}
.author .btn{left:131px;top:669px;width:164px;height:43px;line-height:43px}
.photo-shadow{left:800px;top:322px;width:276px;height:370px;background:var(--grey-shadow)}
.photo{left:786px;top:304px;width:276px;height:370px;background:linear-gradient(180deg,#dfe7ee 0%,#b9c6cf 45%,#c9b9a4 80%,#d8cbb8 100%)}

/* footer */
.site-footer{top:3130px;height:379px;background:var(--black)}
.news-title{top:44px;font-family:"Playfair Display",Georgia,serif;font-size:32px;line-height:44px;color:var(--red)}
.email-field{left:377px;top:110px;width:271px;height:40px;border:2px solid #cfcfcf;color:#bbb;font-size:11px;line-height:36px;padding-left:14px}
.submit{left:662px;top:110px;width:161px;height:40px;line-height:40px;font-size:18px;font-weight:700;letter-spacing:1px}
.social{top:182px;width:56px;height:56px;border-radius:50%;color:var(--white);font-size:10px;font-weight:600;display:flex;align-items:center;justify-content:center}
.social.friendly{left:503px;background:var(--social-blue)}
.social.chirper{left:573px;background:var(--social-sky)}
.social.mail{left:643px;background:var(--social-navy)}
.footer-nav{top:266px;font-size:16px;color:var(--white);word-spacing:4px}
.footer-nav span{margin:0 18px}
.copyright{top:310px;font-size:11px;color:#ddd}
</style>
</head>
<body>

<header class="site-header">
  <div class="brand abs"><span class="brand-mark"></span>Marcus Fellwright</div>
  <nav class="main-nav">
    <a class="active" style="left:723px">Home</a>
    <a style="left:832px">Novels</a>
    <a style="left:946px">World</a>
    <a style="left:1055px">Author</a>
  </nav>
  <div class="nav-blade abs" role="img" aria-label="Small sword ornament under the active link" style="background:linear-gradient(90deg,transparent,var(--red) 40%,var(--red) 70%,#ccc)"></div>
</header>

<section class="hero">
  <div class="hero-art abs" role="img" aria-label="Painted battle scene: a dragon attacking a castle before an army amid fire"></div>
  <h1 class="hero-title abs center">The Legend of Oraveth</h1>
  <p class="hero-sub abs center">To view novel-specific summary information,<br>please select from the titles below.</p>
  <a class="btn abs">Read More</a>
</section>

<section class="novels">
  <h2 class="section-title abs center">Novels</h2>
  <div class="blade abs" role="img" aria-label="Sword ornament"></div>
  <nav class="tabs">
    <a class="active" style="left:185px;width:154px">Summaries</a>
    <a style="left:386px">Excerpts</a>
    <a style="left:545px">Reviews</a>
    <a style="left:697px">Buy Online</a>
    <a style="left:877px">Signed Copies</a>
  </nav>
  <h3 class="sub-title abs center">Summaries</h3>
  <p class="lead abs center">To view novel-specific summary information, please select from the titles below.</p>
  <div class="book-card abs" style="left:246px">
    <span class="book-no">Book One</span>
    <div class="cover" role="img" aria-label="Cover art of The Scarlet Blade" style="background:linear-gradient(#4a3a52,#8a3a3a)"></div>
    <span class="book-name">The Scarlet Blade</span>
  </div>
  <div class="book-card featured abs" style="left:494px">
    <span class="book-no">Book Two</span>
    <div class="cover" role="img" aria-label="Cover art of The Onyx Gate" style="background:linear-gradient(#6a3a1a,#c8501a)"></div>
    <span class="book-name">The Onyx Gate</span>
  </div>
  <div class="book-card abs" style="left:742px">
    <span class="book-no">Book Three</span>
    <div class="cover" role="img" aria-label="Cover art of The Hallowed Amulet" style="background:linear-gradient(#2a4a5a,#6a8a6a)"></div>
    <span class="book-name">The Hallowed Amulet</span>
  </div>
</section>

<section class="world">
  <h2 class="section-title abs center">World</h2>
  <div class="blade abs" role="img" aria-label="Sword ornament"></div>
  <nav class="tabs">
    <a style="left:244px">Maps</a>
    <a style="left:368px">Characters</a>
    <a style="left:546px">Locations</a>
    <a style="left:711px">Artifacts</a>
    <a class="active" style="left:840px;width:121px">Gallery</a>
  </nav>
  <h3 class="sub-title abs center">Art Gallery</h3>
  <p class="lead abs">The following is a collection of artwork pertaining to Marcus's books. Some are professional images, such as cover art and promotional materials. Space is also dedicated to works of art (images, songs, etc) submitted by readers.</p>
  <div class="gallery-item abs" role="img" aria-label="Artwork: a dragon over a burning battlefield" style="left:89px;background:linear-gradient(180deg,#4a5058,#2a2624 55%,#8a3a14)"></div>
  <div class="gallery-item abs" role="img" aria-label="Artwork: twisted trees against a fiery sky" style="left:437px;background:linear-gradient(180deg,#c8702a,#6a2410 60%,#2a0c06)"></div>
  <div class="gallery-item abs" role="img" aria-label="Pencil sketch of a creature in battle" style="left:786px;background:linear-gradient(180deg,#f2f2f2,#c8c8c8)"></div>
</section>

<section class="author">
  <h2 class="section-title abs center">Author</h2>
  <div class="blade abs" role="img" aria-label="Sword ornament"></div>
  <nav class="tabs">
    <a class="active" style="left:290px;width:94px">Bio</a>
    <a style="left:424px">News</a>
    <a style="left:547px">Events</a>
    <a style="left:685px">Interviews</a>
    <a style="left:860px">Q&amp;A</a>
  </nav>
  <h3 class="sub-title bio-title abs">Biography</h3>
  <div class="bio-text abs">
    <p>Weaned on the likes of The Warden of the Vales and Sky Legions, Marcus took to writing fantasy adventure, it seems, almost as soon as he learned to read. By the time he hit grade school, he was writing 30-page stories in lieu of the two or three pages expected of all students on a monthly basis. When at age nine he read Dennis Vale's The Runestones of Merivane, his goal of becoming a fantasy novelist went from child's ambition to hopeless obsession.</p>
    <p>Yet writing was to be a hobby. Even his parents stressed the importance of a "safe" career path. So when the time came, Marcus accepted a scholarship and went off to college, where among his English, writing, and mythology courses, he studied computers, the health sciences,</p>
  </div>
  <a class="btn abs">Read More</a>
  <div class="photo-shadow abs"></div>
  <div class="photo abs" role="img" aria-label="Portrait photo of the author on a beach"></div>
</section>

<footer class="site-footer">
  <h2 class="news-title abs center">Newsletter Signup</h2>
  <div class="email-field abs">Email Address</div>
  <a class="btn submit abs">SUBMIT</a>
  <a class="social friendly abs">Friendly</a>
  <a class="social chirper abs">Chirper</a>
  <a class="social mail abs" aria-label="Email">
    <svg width="28" height="20" viewBox="0 0 28 20"><rect x="1" y="1" width="26" height="18" fill="#fff"/><path d="M1 1 L14 11 L27 1" fill="none" stroke="#d23a3a" stroke-width="2"/></svg>
  </a>
  <p class="footer-nav abs center">Home<span>|</span>Novels<span>|</span>World<span>|</span>Author</p>
  <p class="copyright abs center">Copyright © 2018, MarcusFellwright. All rights reserved.</p>
</footer>

</body>
</html>
```